Harborline Benches business cards

I’d like a business card design that includes my logo, a tag line and my contact info. Black, textured background. My contact info color should match the orange and blue gradients. Tagline under logo: “Solid Oak Benches and Furniture Built to Last Generations”

Target Market(s)

High end furniture buyers

Contact Information for Business Card

Contact info, logo and tagline

```html
<!DOCTYPE html>
<html lang="en">
<head>
<meta charset="utf-8">
<title>Harborline Benches – Business Cards</title>
<link rel="stylesheet" href="https://fonts.googleapis.com/css2?family=Montserrat:wght@700&family=Poppins:wght@300;400;500;600&display=swap">
<style>
  :root {
    --backdrop: #2a2624;
    --card: #1b1b1b;
    --orange: #ee7424;
    --blue: #1553a8;
    --white: #f2f2f2;
    --card-w: 520px;
    --card-h: 297px;
  }
  * { box-sizing: border-box; margin: 0; padding: 0; }
  html, body {
    width: 1200px;
    height: 842px;
    overflow: hidden;
    background: var(--backdrop);
  }
  .sheet {
    width: 1200px;
    height: 842px;
    display: flex;
    align-items: center;
    justify-content: center;
    gap: 60px;
  }
  .card {
    position: relative;
    width: var(--card-w);
    height: var(--card-h);
    background: var(--card);
    box-shadow: 0 14px 30px rgba(0,0,0,.45);
    overflow: hidden;
  }

  /* Contact side */
  .card--contact .band {
    position: absolute;
    left: 0;
    width: 100%;
    background: var(--orange);
  }
  .card--contact .band--top { top: 0; height: 11px; }
  .card--contact .band--bottom { bottom: 0; height: 13px; }
  .contact {
    position: absolute;
    left: 0;
    right: 0;
    top: 48px;
    text-align: center;
    font-family: "Poppins", sans-serif;
    color: var(--white);
  }
  .contact__name {
    font-weight: 600;
    font-size: 24px;
    color: var(--orange);
    line-height: 1.15;
  }
  .contact__role {
    font-weight: 300;
    font-size: 15px;
    letter-spacing: .3px;
  }
  .contact__rule {
    width: 46px;
    height: 2px;
    background: var(--orange);
    margin: 9px auto;
  }
  .contact__lines {
    font-weight: 300;
    font-size: 12.5px;
    line-height: 1.35;
    letter-spacing: .4px;
  }
  .contact__lines .phone { font-size: 15px; letter-spacing: .6px; }
  .contact__lines--address { margin-top: 14px; }

  /* Brand side */
  .accent {
    position: absolute;
    display: flex;
    height: 68px;
  }
  .accent__block { width: 48px; background: var(--orange); }
  .accent__line { width: 4px; background: var(--blue); }
  .accent--left { left: 0; top: 122px; gap: 5px; }
  .accent--right { right: 0; top: 54px; gap: 5px; }
  .brand {
    position: absolute;
    left: 0;
    right: 0;
    top: 96px;
    text-align: center;
  }
  .brand__name {
    font-family: "Montserrat", sans-serif;
    font-weight: 700;
    font-size: 31px;
    color: var(--orange);
    letter-spacing: .3px;
  }
  .tagline {
    position: absolute;
    left: 0;
    right: 0;
    bottom: 44px;
    text-align: center;
    font-family: "Montserrat", sans-serif;
    font-weight: 700;
    font-size: 14.5px;
    color: var(--white);
  }
</style>
</head>
<body>
  <main class="sheet">
    <section class="card card--contact" aria-label="Business card contact side">
      <div class="band band--top"></div>
      <div class="contact">
        <p class="contact__name">Marcus Ellery</p>
        <p class="contact__role">Managing Director</p>
        <div class="contact__rule"></div>
        <div class="contact__lines">
          <p class="phone">044-555 218 640</p>
          <p>INFO@HARBORLINEMAIL.COM</p>
          <p>WWW.HARBORLINEBENCH.COM</p>
        </div>
        <div class="contact__rule"></div>
        <div class="contact__lines contact__lines--address">
          <p>87, ALDERWOOD QUAY LANE WEST</p>
          <p>30718, NORTHFIELD</p>
        </div>
      </div>
      <div class="band band--bottom"></div>
    </section>

    <section class="card card--brand" aria-label="Business card brand side">
      <div class="accent accent--left">
        <div class="accent__block"></div>
        <div class="accent__line"></div>
      </div>
      <div class="accent accent--right">
        <div class="accent__line"></div>
        <div class="accent__block"></div>
      </div>
      <div class="brand">
        <p class="brand__name">Harborline Benches</p>
      </div>
      <p class="tagline">Solid Oak Benches and Furniture Built to Last Generations</p>
    </section>
  </main>
</body>
</html>
```